Business card design for new eCommerce site focusing on integrity and strong businsess tactics

We need a business card that will stand out and be memorable. Something with color that matches our company logo colors. Think high end version of Pactivo. There are 2 logos provided. The parent company is called Amber Ledge Partners and we are presenting a new and very exciting eCommerce site called BrightHarborTrade.example.

Target Market(s)

Our target markets are in the Activities, Food and Beverage, Health and Beauty

Industry/Entity Type

Marketing

Contact Information for Business Card

We have 4 members that need cards...I will provide all info to the winner of the design contest
Business Address is
4870 West 63rd Avenue, Suite C207
Phoenix AZ 85731

Font styles to use
Serif
Sans Serif

Colors

Designer to choose colors to be used in the design.

Requirements
Must have
• The card must be memorable...should be unique in design but must exude integrity and be playful .
• I have provided several colors or our parent company...please feel free to use which ever
Nice to have
• I will leave this up to you. Feel free to use other images of your choosing that wraps around our client.....Activities, Dining, Health, Beauty
Should not have
• just dont be boring

```html
<!DOCTYPE html>
<html lang="en">
<head>
<meta charset="utf-8">
<title>BrightHarborTrade.example – Business Card</title>
<link rel="stylesheet" href="https://fonts.googleapis.com/css2?family=Roboto:wght@400;500;700&display=swap">
<style>
  :root {
    --page-bg: #e4e1dc;
    --card-bg: #eef0ef;
    --brand-blue: #1f5d95;
    --brand-green: #6aa83c;
    --ink: #25292c;
    --icon: #2a4f73;
  }
  * { margin: 0; padding: 0; box-sizing: border-box; }
  html, body {
    width: 1200px; height: 969px; overflow: hidden;
    background: var(--page-bg);
    font-family: "Roboto", Arial, sans-serif;
  }
  .card {
    position: absolute; left: 75px; top: 185px;
    width: 1050px; height: 600px;
    background: var(--card-bg);
    border-radius: 28px;
    overflow: hidden;
    box-shadow: 0 18px 40px rgba(0,0,0,.14);
  }
  .card__art {
    position: absolute; left: 0; top: 0;
    width: 440px; height: 600px;
  }
  .brand {
    position: absolute; right: 50px; top: 88px;
    display: flex; align-items: center; gap: 12px;
  }
  .brand__dot {
    width: 22px; height: 22px; border-radius: 50%;
    background: var(--brand-green);
  }
  .brand__name {
    font-size: 30px; font-weight: 500; color: var(--brand-green);
    white-space: nowrap;
  }
  .details {
    position: absolute; right: 50px; top: 232px;
    text-align: right;
  }
  .person__name {
    font-size: 40px; font-weight: 500; color: var(--brand-blue);
    letter-spacing: 0.5px; line-height: 1.1;
  }
  .person__title {
    margin-top: 4px;
    font-size: 25px; font-weight: 500; color: var(--brand-green);
    letter-spacing: 0.5px;
  }
  .address {
    margin-top: 26px; margin-right: 44px;
    font-size: 24px; color: var(--ink); line-height: 1.4;
    font-style: normal;
  }
  .contacts { margin-top: 18px; list-style: none; }
  .contacts li {
    display: flex; justify-content: flex-end; align-items: center; gap: 14px;
    font-size: 24px; color: var(--ink); line-height: 1.45;
  }
  .contacts svg { width: 26px; height: 26px; flex: none; }
</style>
</head>
<body>
  <article class="card">
    <svg class="card__art" viewBox="0 0 440 600" role="img" aria-label="Brand artwork panel: flowing blue and green figure with leaves">
      <defs>
        <linearGradient id="panelFill" x1="0" y1="0" x2="1" y2="1">
          <stop offset="0" stop-color="#2b7bb8"/>
          <stop offset="0.6" stop-color="#1f5d95"/>
          <stop offset="1" stop-color="#6aa83c"/>
        </linearGradient>
      </defs>
      <path d="M0 0 H330 C420 120 390 260 300 360 C240 430 250 520 300 600 H0 Z" fill="url(#panelFill)"/>
    </svg>

    <header class="brand">
      <span class="brand__dot"></span>
      <span class="brand__name">BrightHarborTrade.example</span>
    </header>

    <section class="details">
      <h1 class="person__name">DANA WHITFIELD</h1>
      <p class="person__title">CEO/FOUNDER</p>
      <address class="address">4870 West 63rd Avenue<br>Suite C207, Phoenix AZ 85731</address>
      <ul class="contacts">
        <li>555 214 7380
          <svg viewBox="0 0 24 24" aria-hidden="true"><path fill="var(--icon)" d="M6.6 10.8a15 15 0 0 0 6.6 6.6l2.2-2.2c.3-.3.7-.4 1-.2 1.1.4 2.3.6 3.6.6.6 0 1 .4 1 1V20c0 .6-.4 1-1 1A17 17 0 0 1 3 4c0-.6.4-1 1-1h3.5c.6 0 1 .4 1 1 0 1.3.2 2.5.6 3.6.1.3 0 .7-.2 1z"/></svg>
        </li>
        <li>555 903 6127
          <svg viewBox="0 0 24 24" aria-hidden="true"><rect x="6.5" y="2" width="11" height="20" rx="2" fill="none" stroke="var(--icon)" stroke-width="2"/><circle cx="12" cy="18.5" r="1.2" fill="var(--icon)"/></svg>
        </li>
        <li>dana@brightharbortrade.example
          <svg viewBox="0 0 24 24" aria-hidden="true"><rect x="3" y="5" width="18" height="14" rx="1.5" fill="var(--icon)"/><path d="M3.5 6l8.5 7 8.5-7" fill="none" stroke="#eef0ef" stroke-width="1.6"/></svg>
        </li>
        <li>www.brightharbortrade.example
          <svg viewBox="0 0 24 24" aria-hidden="true"><circle cx="12" cy="12" r="9" fill="var(--icon)"/><path d="M3 12h18M12 3c3 3 3 15 0 18M12 3c-3 3-3 15 0 18" fill="none" stroke="#eef0ef" stroke-width="1.3"/></svg>
        </li>
      </ul>
    </section>
  </article>
</body>
</html>
```